Specialised investor in e-mobility and energy wants business card design

We need a business card design that fits our existing corporate design. <The look and feel must be 'sharp'/'clean', dynamic, communicate momentum, professionalism etc (as one would imagine from a firm in the financial sector). We like the idea of a reverse-side of the card that includes the logo, and the name and contact details on the other. We expect the deliverable to be whatever format might be required to be able to get cards printed directly by a service such as kelmo press. Our website is www.zub.capital

```html
<!DOCTYPE html>
<html lang="en">
<head>
<meta charset="utf-8">
<title>Zub Capital – Business Card</title>
<link href="https://fonts.googleapis.com/css2?family=Roboto:wght@400;500;700&display=swap" rel="stylesheet">
<style>
  :root {
    --backdrop: #d2d3d6;
    --card: #ffffff;
    --forest: #2b4a23;
    --leaf: #7aad3f;
    --ink: #2a3a22;
  }
  * { margin: 0; padding: 0; box-sizing: border-box; }
  html, body {
    width: 900px; height: 1200px; overflow: hidden;
    background: var(--backdrop);
    font-family: "Roboto", Arial, sans-serif;
  }
  .canvas { position: relative; width: 900px; height: 1200px; }
  .card {
    position: absolute; left: 165px; width: 570px; height: 374px;
    background: var(--card);
  }
  .card--front { top: 190px; }
  .card--back { top: 636px; }

  .wordmark {
    position: absolute; left: 0; right: 0; top: 150px;
    display: flex; justify-content: center; align-items: center; gap: 14px;
    color: var(--forest); font-weight: 500; font-size: 50px; letter-spacing: 0.5px;
  }
  .wordmark__dot {
    width: 14px; height: 14px; border-radius: 50%; background: var(--leaf);
  }

  .identity {
    position: absolute; right: 302px; top: 166px; text-align: right;
  }
  .identity__name {
    color: var(--leaf); font-weight: 700; font-size: 23px; line-height: 28px;
  }
  .identity__role {
    color: var(--ink); font-size: 13.5px; line-height: 18px; letter-spacing: 0.4px;
  }
  .divider {
    position: absolute; left: 284px; top: 158px; width: 2px; height: 58px;
    background: var(--forest);
  }
  .contacts {
    position: absolute; left: 303px; top: 158px; list-style: none;
  }
  .contacts__item {
    display: flex; align-items: center; gap: 7px;
    height: 22px; color: var(--ink); font-size: 14px; letter-spacing: 0.8px;
  }
  .contacts__icon { width: 12px; height: 12px; fill: var(--leaf); flex: none; }
</style>
</head>
<body>
<div class="canvas">
  <section class="card card--front">
    <div class="wordmark"><span class="wordmark__dot"></span><span>Zub Capital</span></div>
  </section>

  <section class="card card--back">
    <div class="identity">
      <p class="identity__name">Marc Hollen</p>
      <p class="identity__role">Partner</p>
    </div>
    <div class="divider"></div>
    <ul class="contacts">
      <li class="contacts__item">
        <svg class="contacts__icon" viewBox="0 0 24 24"><path d="M6.6 10.8a15.1 15.1 0 0 0 6.6 6.6l2.2-2.2a1 1 0 0 1 1-.25 11.4 11.4 0 0 0 3.6.57 1 1 0 0 1 1 1V20a1 1 0 0 1-1 1A17 17 0 0 1 3 4a1 1 0 0 1 1-1h3.5a1 1 0 0 1 1 1c0 1.25.2 2.45.57 3.57a1 1 0 0 1-.25 1z"/></svg>
        <span>+41 79514 2870</span>
      </li>
      <li class="contacts__item">
        <svg class="contacts__icon" viewBox="0 0 24 24"><path d="M2 5h20v14H2z M3.5 6.5 12 12.5l8.5-6" fill="none" stroke="#7aad3f" stroke-width="2"/><path d="M2 5h20l-10 7z"/></svg>
        <span>marc@zub.capital</span>
      </li>
      <li class="contacts__item">
        <svg class="contacts__icon" viewBox="0 0 24 24"><circle cx="12" cy="12" r="10" fill="none" stroke="#7aad3f" stroke-width="2"/><path d="M2 12h20M12 2c3 3 3 17 0 20M12 2c-3 3-3 17 0 20" fill="none" stroke="#7aad3f" stroke-width="1.6"/></svg>
        <span>www.zub.capital</span>
      </li>
    </ul>
  </section>
</div>
</body>
</html>
```